Building company buisness cards

We are looking for a sharp modern new look for our business cards.We are a New Zealand based company that specialises in house and land packages.We have attached a photo of the current logo and would like to see if it can be improved somehow if needed.We are open to any colours but we have chosen Black and White at this stage. Feel free to change the font and make the logo smarter looking.Play with the colours and see what looks best.We want a card that looks so good know one will want to throw it away!

Target Market(s)

Building profesonals, home buyers

Industry/Entity Type

Building

Contact Information for Business Card

Garrick Tenwood
0275390628
garrickt@hartvale.co.nz

Font styles to use
Serif
Sans Serif

Colors

Designer to choose colors to be used in the design.

Requirements
Must have
• Just the logo on one side and details on the other
• Clean simple looking card
Nice to have
• Round corners and detail like raised or spot UV
• Something that stands out
Should not have
• To title needed, Director etc

```html
<!DOCTYPE html>
<html lang="en">
<head>
<meta charset="utf-8">
<title>Hartvale Business Cards</title>
<link href="https://fonts.googleapis.com/css2?family=Playfair+Display:wght@900&family=Open+Sans:wght@400;700&display=swap" rel="stylesheet">
<style>
  :root {
    --backdrop: #2b2b2d;
    --card-black: #0a0a0f;
    --card-white: #ffffff;
    --ink-light: #f2f2f2;
    --ink-dark: #111114;
  }
  html, body {
    margin: 0;
    padding: 0;
    width: 1200px;
    height: 885px;
    overflow: hidden;
    background: var(--backdrop);
  }
  .canvas {
    position: relative;
    width: 1200px;
    height: 885px;
  }
  .card {
    position: absolute;
    left: 340px;
    width: 520px;
    height: 318px;
    border-radius: 22px;
    overflow: hidden;
    background: var(--card-black);
    box-shadow: 0 10px 30px rgba(0,0,0,0.45);
  }
  .card--back { top: 105px; }
  .card--front { top: 462px; }

  .brand-name {
    font-family: "Playfair Display", Georgia, serif;
    font-weight: 900;
    letter-spacing: -0.5px;
    line-height: 1;
  }
  .card--back .brand-name {
    position: absolute;
    right: 30px;
    bottom: 34px;
    font-size: 46px;
    color: var(--ink-light);
  }

  .front-panel {
    position: absolute;
    left: 0;
    top: 0;
    width: 208px;
    height: 100%;
    background: var(--card-white);
  }
  .front-logo {
    position: absolute;
    left: 22px;
    top: 150px;
    display: flex;
    align-items: center;
  }
  .front-logo .brand-name {
    font-size: 40px;
    color: var(--ink-dark);
  }
  .brand-dot {
    position: absolute;
    left: 190px;
    top: 108px;
    width: 32px;
    height: 32px;
    border-radius: 50%;
    border: 3px solid var(--ink-light);
    background: var(--card-black);
  }

  .contact {
    position: absolute;
    left: 262px;
    top: 100px;
    font-family: "Open Sans", Arial, sans-serif;
    color: var(--ink-light);
  }
  .contact__name {
    margin: 0 0 8px;
    font-size: 17px;
    font-weight: 700;
  }
  .contact__list {
    list-style: none;
    margin: 0;
    padding: 0 0 0 22px;
  }
  .contact__item {
    display: flex;
    align-items: center;
    gap: 8px;
    font-size: 14px;
    line-height: 20px;
  }
  .contact__icon {
    width: 12px;
    height: 12px;
    fill: var(--ink-light);
    flex: none;
  }
</style>
</head>
<body>
<div class="canvas">
  <section class="card card--back" aria-label="Card back">
    <span class="brand-name">Hartvale</span>
  </section>

  <section class="card card--front" aria-label="Card front">
    <div class="front-panel"></div>
    <div class="front-logo"><span class="brand-name">Hartvale</span></div>
    <div class="brand-dot"></div>

    <div class="contact">
      <p class="contact__name">Garrick Tenwood</p>
      <ul class="contact__list">
        <li class="contact__item">
          <svg class="contact__icon" viewBox="0 0 12 12"><path d="M1 4c0-2 2-3 5-3s5 1 5 3l-2 1-1-1H4L3 5 1 4zM3 6h6l1 5H2z"/></svg>
          0275390628
        </li>
        <li class="contact__item">
          <svg class="contact__icon" viewBox="0 0 12 12"><path d="M1 3h10v1L6 7 1 4zM1 5l5 3 5-3v5H1z"/></svg>
          garrickt@hartvale.co.nz
        </li>
        <li class="contact__item">
          <svg class="contact__icon" viewBox="0 0 12 12"><circle cx="6" cy="6" r="5"/></svg>
          www.hartvale.co.nz
        </li>
      </ul>
    </div>
  </section>
</div>
</body>
</html>
```